Ausgefallene Verpackung für Neuartige Hunde Leine
Zielgruppe
ZIELGRUPPE: HUNDEHALTER
Aufgabenstellung
Das Projekt ist bis zum 15.01.2021 online. Bis dahin werden noch Design Vorschläge angenommen da es durch Feiertage zu Verzögerungen kam.
Die Vorgaben wäre eine interessante nicht stereotypische Verpackung bzw Halterung für eine Hundeleine zu entwickeln wobei die Vorzüge der Leine ausreichend und ansprechend illustriert und bestenfalls die Handhabung (auf der Rückseite) erklärt ist.
Bitte 'outside the box' denken. Es muss im Regal irgendwie auffallen das das Produkt anders ist als die anderen Leinen.
Ausserdem soll möglichst wenig Verpackunsmüll entstehen und kein Plastik verwendet werden.
Ein Bild im Sinne von Foto soll nicht direkt darauf, aber es soll anhand der Verpackung ersichtlich werden um was es sich handelt und welchen Nutzen die Leine hat.
Projektbeschreibung:
Es geht um eine Antizugleine welche in einen einfachen System dem Hund um den Brust gelegt wird und mit einem Karabiner dann am Halsband wie eine normale Leine befestigt wird. Sobald er anzieht gibt es einen leichten Druck und er hört auf zuziehen.
Gerne schicke ich Ihnen ein Foto der Leine ggf am Hund.
Das gute ist das man z. B. kein extra Haltegeschirr braucht welches man umständlich anziehen muss oder ein Halsband was sich am Hals zuzieht.
Gerade für ältere Menschen von Vorteil wenn der Hund nicht so (ruckartig) anzieht.
Ohne grosses Training wird die ungehemmt Vowärtsbewegung gehemmt.
UPDATE AUF DESIGNER ANMERKUNGEN:
Es geht zuerst um die Verpackung und deren Form. Danach auf den Inhalt
Schlagworte:
- vermindert das ziehen
- eine Größe für alle
- kein extra Haltegeschirr notwendig
- kein zuziehen der Kehle
- Ausbruchsicher
- hergestellt in Deutschland
1) Anleitungsbildchen zu kleine Dateigröße:
= Die Anleitungsbildchen sind nur zur Verdeutlichung/ Erklärung der Anwendung der Leine. Falls Sie diese Erklärungen verwenden möchten dienen dienen die zur Zeit als Pla..

```html
<!DOCTYPE html>
<html lang="de">
<head>
<meta charset="utf-8">
<title>Leinenfreund – Antizugleine Verpackung</title>
<link rel="stylesheet" href="https://fonts.googleapis.com/css2?family=Quicksand:wght@500;700&display=swap">
<style>
  :root {
    --kraft: #c9a384;
    --kraft-dark: #b48d6e;
    --ink: #1f1a17;
    --paw-red: #a3161b;
    --backdrop: #ffffff;
  }
  * { margin: 0; padding: 0; box-sizing: border-box; }
  html, body { width: 1200px; height: 1200px; overflow: hidden; background: var(--backdrop); }
  body { position: relative; font-family: "Quicksand", sans-serif; color: var(--ink); }

  .hang-card {
    position: absolute; left: 150px; top: 90px; width: 420px; height: 1020px;
    background: var(--kraft);
  }
  .hang-hole {
    position: absolute; left: 50%; top: 28px; width: 64px; height: 20px;
    transform: translateX(-50%); border-radius: 10px; background: var(--backdrop);
  }
  .brand-block {
    position: absolute; left: 30px; top: 110px; width: 360px; height: 360px;
  }
  .brand-disc {
    position: absolute; left: 35px; top: 70px; width: 290px; height: 290px;
    border-radius: 50%; background: var(--ink);
  }
  .brand-name {
    position: absolute; left: 0; right: 0; top: 192px; text-align: center;
    font-weight: 700; font-size: 36px; line-height: 46px; color: var(--kraft);
  }
  .size-arc { position: absolute; left: 0; top: 475px; width: 420px; height: 120px; }
  .size-arc text { font-family: "Quicksand", sans-serif; font-weight: 500; font-size: 19px; fill: var(--ink); }
  .product-title {
    position: absolute; left: 0; right: 0; top: 560px; text-align: center;
    font-weight: 700; font-size: 40px; line-height: 50px;
  }
  .benefits {
    position: absolute; left: 70px; top: 625px; list-style: none;
    font-weight: 500; font-size: 19px; line-height: 30px;
  }
  .benefits li { display: flex; align-items: center; gap: 8px; }
  .benefits svg { width: 18px; height: 18px; flex: none; }

  .box-panel {
    position: absolute; left: 640px; top: 420px; width: 440px; height: 560px;
    background: var(--kraft-dark);
  }
  .size-mark { position: absolute; left: 40px; top: 100px; width: 360px; height: 360px; }
  .size-mark text { font-family: "Quicksand", sans-serif; font-weight: 500; font-size: 26px; fill: var(--ink); }
  .size-mark .colour-name { font-size: 40px; }
</style>
</head>
<body>
  <section class="hang-card">
    <div class="hang-hole"></div>
    <div class="brand-block">
      <div class="brand-disc"></div>
      <div class="brand-name">Leinenfreund</div>
    </div>
    <svg class="size-arc" viewBox="0 0 420 120">
      <path id="cardArc" d="M40 115 Q90 50 200 40" fill="none"/>
      <text><textPath href="#cardArc">eine Größe für alle</textPath></text>
    </svg>
    <h1 class="product-title">Antizugleine</h1>
    <ul class="benefits">
      <li><svg viewBox="0 0 20 20"><path d="M3 11 L8 16 L17 4" fill="none" stroke="currentColor" stroke-width="3"/></svg>vermindert das ziehen</li>
      <li><svg viewBox="0 0 20 20"><path d="M3 11 L8 16 L17 4" fill="none" stroke="currentColor" stroke-width="3"/></svg>kein zuziehen der Kehle</li>
      <li><svg viewBox="0 0 20 20"><path d="M3 11 L8 16 L17 4" fill="none" stroke="currentColor" stroke-width="3"/></svg>kein extra Haltegeschirr nötig</li>
      <li><svg viewBox="0 0 20 20"><path d="M3 11 L8 16 L17 4" fill="none" stroke="currentColor" stroke-width="3"/></svg>ausbruchsicher</li>
      <li><svg viewBox="0 0 20 20"><path d="M3 11 L8 16 L17 4" fill="none" stroke="currentColor" stroke-width="3"/></svg>hergestellt in Deutschland</li>
    </ul>
  </section>

  <section class="box-panel">
    <svg class="size-mark" viewBox="0 0 360 360">
      <path id="boxArc" d="M72 242 A125 125 0 0 1 202 57" fill="none"/>
      <text><textPath href="#boxArc">eine Größe für alle</textPath></text>
      <path d="M303 202 A125 125 0 0 1 137 297" fill="none" stroke="var(--ink)" stroke-width="3"/>
      <text class="colour-name" x="180" y="188" text-anchor="middle">ROT</text>
      <ellipse cx="180" cy="242" rx="42" ry="38" fill="var(--paw-red)" role="img" aria-label="Rote Pfoten-Grafik als Farbkennzeichnung"/>
    </svg>
  </section>
</body>
</html>
```